Alterations to existing business card

Here is my current logo and I want the "cafe and bar" taken off with just the words Lumo and our slogan "Savour every sip" on the card, Plus the logo.
Our Current Business Card is currently 5.5cm by 5.5cm and would like it to remain like this thanks.
The loyalty card can be 10 squares with the logo specifying the 10th coffee free. I would like the cheapest option please.
Also on our business card would like the Facebook logo and instagram Logo with TAZALUMO27 as link to our photos on instagram.

Keep Colour schemes the same please.

On the business cards

Dale Brinton Director
0427916038
dale27lumo@mailvista.test

Paula Ferrisi Principal
0428571963
paulumo@mailvista.test

Thanks Dale

Industry/Entity Type

Business

```html
<!DOCTYPE html>
<html lang="en">
<head>
<meta charset="utf-8">
<title>Lumo — Business Card and Loyalty Card</title>
<link rel="stylesheet" href="https://fonts.googleapis.com/css2?family=Questrial&display=swap">
<style>
  :root {
    --page-bg: #4a4a4a;
    --card-white: #ffffff;
    --gold: #eea83a;
    --gold-light: #f7dc78;
    --gold-deep: #e9a537;
    --ink: #151515;
    --text-grey: #444444;
    --accent-orange: #eba43c;
  }
  * { box-sizing: border-box; margin: 0; padding: 0; }
  html, body {
    width: 1105px; height: 1200px; overflow: hidden;
    background: var(--page-bg);
    font-family: "Questrial", "Century Gothic", sans-serif;
  }
  .canvas { position: relative; width: 1105px; height: 1200px; }

  /* Business card */
  .business-card {
    position: absolute; left: 124px; top: 110px;
    width: 449px; height: 449px;
    background: var(--card-white);
    overflow: hidden;
  }
  .brand-mark {
    position: absolute; left: 254px; top: 35px;
    width: 124px; height: 124px;
    border: 3px solid var(--accent-orange); border-radius: 50%;
  }
  .brand-name {
    position: absolute; right: 48px; top: 166px;
    font-size: 48px; letter-spacing: 2px; color: var(--ink); line-height: 1;
  }
  .brand-slogan {
    position: absolute; right: 48px; top: 217px;
    font-size: 14px; letter-spacing: 1.5px; color: var(--accent-orange); line-height: 1;
  }
  .person-name {
    position: absolute; left: 37px; top: 276px;
    font-size: 27px; letter-spacing: 1px; color: var(--accent-orange); line-height: 1;
  }
  .person-role {
    position: absolute; left: 37px; top: 311px; right: 48px;
    display: flex; align-items: center; gap: 8px;
    font-size: 19px; letter-spacing: 1px; color: var(--ink); line-height: 1;
  }
  .person-role::after { content: ""; flex: 1; height: 1.5px; background: var(--ink); }
  .contact-line {
    position: absolute; left: 37px;
    display: flex; align-items: center; gap: 10px;
    font-size: 19px; color: var(--text-grey); line-height: 1;
  }
  .contact-line svg { width: 18px; height: 18px; }
  .contact-phone { top: 352px; }
  .contact-email { top: 381px; }
  .card-band { position: absolute; left: 0; bottom: 0; width: 449px; height: 15px; }

  /* Loyalty card */
  .loyalty-card {
    position: absolute; left: 500px; top: 628px;
    width: 449px; height: 449px;
    background: linear-gradient(90deg, var(--gold-deep) 0%, var(--gold) 35%, var(--gold-light) 100%);
  }
  .loyalty-mark {
    position: absolute; left: 134px; top: 30px;
    width: 166px; height: 166px;
    border: 3px solid var(--ink); border-radius: 50%;
    display: flex; align-items: center; justify-content: center;
    font-size: 38px; letter-spacing: 2px; color: var(--ink);
  }
  .stamp-grid {
    position: absolute; left: 33px; top: 222px;
    display: grid; grid-template-columns: repeat(5, 66px);
    column-gap: 10px; row-gap: 17px;
  }
  .stamp {
    width: 66px; height: 66px; border-radius: 50%;
    border: 2px solid var(--ink);
    display: flex; align-items: center; justify-content: center;
  }
  .stamp svg { width: 44px; height: 44px; }
  .stamp-free {
    background: var(--accent-orange);
    font-size: 17px; font-weight: 700; color: var(--ink); letter-spacing: 0.5px;
  }
  .loyalty-footer {
    position: absolute; left: 45px; right: 45px; top: 400px;
    display: flex; align-items: center; gap: 8px;
    font-size: 18px; letter-spacing: 1px; color: var(--ink); line-height: 1;
  }
  .loyalty-footer::before, .loyalty-footer::after {
    content: ""; flex: 1; height: 1.5px; background: var(--ink);
  }
  .social-dot { width: 18px; height: 18px; border-radius: 50%; background: var(--ink); }
</style>
</head>
<body>
<main class="canvas">

  <section class="business-card" aria-label="Business card">
    <div class="brand-mark" aria-hidden="true"></div>
    <div class="brand-name">LUMO</div>
    <div class="brand-slogan">SAVOUR EVERY SIP</div>

    <div class="person-name">DALE BRINTON</div>
    <div class="person-role">DIRECTOR</div>

    <div class="contact-line contact-phone">
      <svg viewBox="0 0 18 18" aria-hidden="true">
        <rect x="4.5" y="1" width="9" height="16" rx="1.5" fill="none" stroke="var(--accent-orange)" stroke-width="1.6"/>
        <line x1="7.5" y1="14" x2="10.5" y2="14" stroke="var(--accent-orange)" stroke-width="1.4"/>
      </svg>
      <span>0427916038</span>
    </div>
    <div class="contact-line contact-email">
      <svg viewBox="0 0 18 18" aria-hidden="true">
        <rect x="1" y="4" width="16" height="11" fill="var(--accent-orange)"/>
        <polyline points="1,4 9,10.5 17,4" fill="none" stroke="#fff" stroke-width="1.4"/>
      </svg>
      <span>dale27lumo@mailvista.test</span>
    </div>

    <svg class="card-band" viewBox="0 0 449 15" aria-hidden="true">
      <defs>
        <linearGradient id="band-gold" x1="0" x2="1" y1="0" y2="0">
          <stop offset="0" stop-color="var(--gold-deep)"/>
          <stop offset="1" stop-color="var(--gold-light)"/>
        </linearGradient>
      </defs>
      <polygon points="0,0 330,0 325,15 0,15" fill="url(#band-gold)"/>
      <polygon points="336,0 449,0 449,15 331,15" fill="var(--ink)"/>
    </svg>
  </section>

  <section class="loyalty-card" aria-label="Loyalty card">
    <svg width="0" height="0" style="position:absolute" aria-hidden="true">
      <symbol id="cup-icon" viewBox="0 0 44 44">
        <path d="M9 19 h22 v6 a9 9 0 0 1 -9 9 h-4 a9 9 0 0 1 -9 -9 z" fill="var(--ink)"/>
        <path d="M31 21 h3 a4 4 0 0 1 0 8 h-4" fill="none" stroke="var(--ink)" stroke-width="2"/>
        <rect x="5" y="35" width="30" height="2.5" rx="1.2" fill="var(--ink)"/>
        <path d="M17 16 c-2 -3 2 -5 0 -8 M22 16 c-2 -3 2 -5 0 -8" fill="none" stroke="var(--ink)" stroke-width="1.4"/>
      </symbol>
    </svg>

    <div class="loyalty-mark">LUMO</div>

    <div class="stamp-grid">
      <div class="stamp"><svg aria-hidden="true"><use href="#cup-icon"/></svg></div>
      <div class="stamp"><svg aria-hidden="true"><use href="#cup-icon"/></svg></div>
      <div class="stamp"><svg aria-hidden="true"><use href="#cup-icon"/></svg></div>
      <div class="stamp"><svg aria-hidden="true"><use href="#cup-icon"/></svg></div>
      <div class="stamp"><svg aria-hidden="true"><use href="#cup-icon"/></svg></div>
      <div class="stamp"><svg aria-hidden="true"><use href="#cup-icon"/></svg></div>
      <div class="stamp"><svg aria-hidden="true"><use href="#cup-icon"/></svg></div>
      <div class="stamp"><svg aria-hidden="true"><use href="#cup-icon"/></svg></div>
      <div class="stamp"><svg aria-hidden="true"><use href="#cup-icon"/></svg></div>
      <div class="stamp stamp-free">FREE</div>
    </div>

    <div class="loyalty-footer">
      <span class="social-dot" aria-hidden="true"></span>
      <span>TAZALUMO27</span>
    </div>
  </section>

</main>
</body>
</html>
```